Resposive web site in 4 languages + image gallery + logo design

We need a web page, which will work on all devices.
I have uploaded web page concept.
Company name: Praxelun
Industry/Entity Type
It Company
Logo Text
quality matters
Coding
Coded - Design and coding required
Number of Pages Required
1 page

```html
<!DOCTYPE html>
<html lang="en">
<head>
<meta charset="utf-8">
<title>Praxelun — Woodworks, Stoneworks &amp; Restoration</title>
<link rel="stylesheet" href="https://fonts.googleapis.com/css2?family=Raleway:wght@500;600;700;800&family=Open+Sans:wght@400;600;700&display=swap">
<style>
:root{
  --orange:#e0962c;
  --orange-dark:#c98220;
  --ink:#333333;
  --text:#6b6b6b;
  --rule:#d6d6d6;
  --about-bg:#efefef;
  --white:#ffffff;
  --header-bg:rgba(20,16,12,.72);
  --contact-bg:#4a3e33;
}
*{box-sizing:border-box;margin:0;padding:0}
html,body{width:1200px;height:2459px;overflow:hidden}
body{font-family:"Open Sans",Arial,sans-serif;color:var(--text);background:var(--white);position:relative}
.abs{position:absolute}

/* header + hero */
.hero{left:0;top:0;width:1200px;height:452px;background:radial-gradient(ellipse at 70% 45%,#b08560 0%,#7a5536 40%,#3d2a1c 100%)}
.site-header{left:0;top:4px;width:1200px;height:62px;background:var(--header-bg)}
.hero-topline{left:0;top:0;width:1200px;height:4px;background:var(--orange)}
.brand{display:flex;align-items:center;gap:8px;font-family:"Raleway",sans-serif;font-weight:700;font-size:22px;color:var(--white);letter-spacing:.5px}
.brand-mark{width:16px;height:16px;background:var(--orange)}
.main-nav{left:621px;display:flex;font-family:"Raleway",sans-serif;font-weight:700;font-size:13px;color:var(--white)}
.main-nav span{margin-right:45px}
.lang{left:946px;width:86px;height:33px;border:1px solid #ccc;display:flex;font-family:"Raleway",sans-serif;font-weight:700;font-size:12px;color:var(--white)}
.lang .code{flex:1;display:flex;align-items:center;justify-content:center}
.lang .caret{width:30px;background:var(--orange);display:flex;align-items:center;justify-content:center}
.social-dot{left:1052px;width:46px;height:46px;border-radius:50%;background:#3b5998}
.hero-title{left:0;top:195px;width:1200px;text-align:center;font-family:"Raleway",sans-serif;font-weight:800;font-size:84px;letter-spacing:8px;color:var(--white);text-shadow:0 3px 6px rgba(0,0,0,.45)}
.hero-arrow{top:220px;width:44px;height:44px;border-radius:50%;background:rgba(0,0,0,.35);display:flex;align-items:center;justify-content:center}
.hero-dots{left:566px;top:403px;display:flex;gap:5px}
.hero-dots i{width:20px;height:20px;border-radius:50%;border:2px solid var(--white);display:block}
.hero-dots i.on{background:var(--orange)}

/* estimate band */
.estimate{left:0;top:452px;width:1200px;height:78px;background:var(--orange)}
.estimate-text{left:254px;top:26px;font-weight:700;font-size:23px;color:var(--white)}
.btn-quote{left:778px;top:15px;width:168px;height:46px;border-radius:4px;background:linear-gradient(#f2f2f2,#c9c9c9);display:flex;align-items:center;justify-content:center;font-family:"Raleway",sans-serif;font-weight:700;font-size:16px;color:#444}

/* section headings */
.section-title{width:1200px;left:0;text-align:center;font-family:"Raleway",sans-serif;font-weight:700;font-size:25px;color:var(--ink)}
.section-title .cap{color:var(--orange);font-size:38px}
.section-title.light{color:var(--white)}

/* services */
.service-photo{border:3px solid var(--white);box-shadow:0 0 0 1px #d8d8d8}
.service-name{font-family:"Raleway",sans-serif;font-weight:600;font-size:22px;color:var(--ink)}
.service-copy{font-size:12px;line-height:29px;color:var(--text)}
.tags{display:flex;gap:12px;font-weight:600;font-size:12.5px;color:#444;align-items:center;white-space:nowrap}
.tags span{display:flex;align-items:center;gap:5px}
.tags svg{width:16px;height:16px;flex:none}
.tags.compact{gap:8px;font-size:12px}
.tags.compact span{gap:4px}
.tags.compact svg{width:15px;height:15px}
.divider{left:98px;width:1003px;height:1px;background:var(--rule)}

/* about */
.about{left:0;top:1510px;width:1200px;height:444px;background:var(--about-bg)}
.about-title{left:657px;top:36px;font-family:"Raleway",sans-serif;font-weight:700;font-size:25px;color:var(--ink)}
.about-title .cap{color:var(--orange);font-size:38px}
.about-copy{left:657px;top:88px;width:432px;font-size:12px;line-height:28px;color:var(--text)}
.about-copy p+p{margin-top:27px}
.signoff{left:657px;top:335px;font-weight:700;font-size:13px;color:var(--ink);line-height:26px}
.signoff strong{color:var(--orange);font-size:16px;display:block}

/* contact */
.contact{left:0;top:1954px;width:1200px;height:439px;background:radial-gradient(ellipse at 20% 60%,#6a5846 0%,#473b30 55%,#2f2620 100%)}
.col-title{font-weight:700;font-size:15px;color:var(--white)}
.info-row{left:98px;display:flex;align-items:center;gap:18px;font-size:12px;line-height:17px;color:var(--white)}
.info-icon{width:38px;height:38px;border:2px solid var(--white);border-radius:50%;display:flex;align-items:center;justify-content:center;flex:none}
.social-row{left:98px;top:2336px;display:flex;gap:15px}
.social-row i{width:26px;height:26px;border-radius:4px;background:var(--white);display:block}
.field-label{font-size:11px;color:var(--white)}
.field{background:var(--white)}
.btn-send{left:1015px;top:2326px;width:85px;height:34px;border:2px solid var(--white);display:flex;align-items:center;justify-content:center;font-weight:700;font-size:12px;color:var(--white)}

.site-footer{left:0;top:2393px;width:1200px;height:66px;background:var(--orange);display:flex;align-items:center;justify-content:center;font-size:11.5px;color:var(--white)}
</style>
</head>
<body>

<section class="abs hero" role="img" aria-label="Photo of a craftsman's hands marking a timber plank in a woodshop with wood shavings"></section>
<div class="abs hero-topline"></div>
<header class="abs site-header">
  <div class="abs brand" style="left:100px;top:14px"><span class="brand-mark"></span>PRAXELUN</div>
  <nav class="abs main-nav" style="top:21px"><span>SERVICES</span><span>ABOUT US</span><span>CONTACT US</span></nav>
  <div class="abs lang" style="top:12px">
    <span class="code">ENG</span>
    <span class="caret"><svg width="10" height="6" viewBox="0 0 10 6"><path d="M0 0h10L5 6z" fill="#fff"/></svg></span>
  </div>
  <span class="abs social-dot" style="top:6px" aria-label="Social page"></span>
</header>
<h1 class="abs hero-title">PRAXELUN</h1>
<span class="abs hero-arrow" style="left:30px"><svg width="12" height="20" viewBox="0 0 12 20"><path d="M10 2L2 10l8 8" stroke="#fff" stroke-width="2.5" fill="none"/></svg></span>
<span class="abs hero-arrow" style="left:1126px"><svg width="12" height="20" viewBox="0 0 12 20"><path d="M2 2l8 8-8 8" stroke="#fff" stroke-width="2.5" fill="none"/></svg></span>
<div class="abs hero-dots"><i class="on"></i><i></i><i></i></div>

<section class="abs estimate">
  <p class="abs estimate-text">ARE YOU INTERESTED IN AN ESTIMATE?</p>
  <span class="abs btn-quote">GET A QUOTE</span>
</section>

<h2 class="abs section-title" style="top:558px">OUR <span class="cap">S</span>ERVICES</h2>

<!-- Woodworks -->
<div class="abs service-photo" style="left:98px;top:633px;width:377px;height:236px;background:linear-gradient(135deg,#caa27a,#8a6443 60%,#5a3f2a)" role="img" aria-label="Photo of woodworking tools, a hammer and pencil on a workbench"></div>
<h3 class="abs service-name" style="left:509px;top:629px">Woodworks</h3>
<p class="abs service-copy" style="left:512px;top:675px;width:535px">Timber is, in essence, a natural and warm material. Wood is also relatively durable and easy to work with, which has made it a favourite of builders throughout history. Our goal is to offer suitable products and quality furniture with installation and after-sales service to all of our clients. In order to achieve this, we're this category gallery ready to help our clients in all stages of construction from design to production and maintenance.</p>
<div class="abs tags" style="left:512px;top:841px">
  <span><svg viewBox="0 0 18 18"><path d="M4 2h10v7H4zM3 9h12v3H3zM4 12v5M14 12v5" stroke="#2aa64a" stroke-width="2" fill="none"/></svg>Furniture</span>
  <span><svg viewBox="0 0 18 18"><rect x="2" y="3" width="14" height="12" fill="#f0b43a"/><path d="M9 3v12M2 9h14" stroke="#fff" stroke-width="1.5"/></svg>Windows</span>
  <span><svg viewBox="0 0 18 18"><path d="M4 1h10v17H4z" fill="#3a7bd5"/><circle cx="11.5" cy="10" r="1" fill="#fff"/></svg>Doors</span>
  <span><svg viewBox="0 0 18 18"><path d="M2 16h4v-4h4V8h4V4h3" stroke="#9b59d6" stroke-width="2" fill="none"/></svg>Staircases</span>
  <span><svg viewBox="0 0 18 18"><circle cx="9" cy="7" r="5" fill="#2eb0c0"/><rect x="3" y="13" width="12" height="3" fill="#2eb0c0"/></svg>Woodcarving</span>
  <span><svg viewBox="0 0 18 18"><path d="M2 15l8-10 6 4-6 6z" fill="#e8b526"/></svg>Graining</span>
</div>

<div class="abs divider" style="top:898px"></div>

<!-- Stoneworks -->
<h3 class="abs service-name" style="left:95px;top:929px">Stoneworks</h3>
<p class="abs service-copy" style="left:98px;top:975px;width:532px">The natural stone found in the ground has been used in construction for centuries because of its durability. A structure built by a skilled craftsman from natural stone is unique, genuine and durable, and perfect for our bracing climate.<br>Our experienced craftsmen are ready to help you in all stages of construction from planning to completion.</p>
<div class="abs tags compact" style="left:98px;top:1142px">
  <span><svg viewBox="0 0 18 18"><path d="M1 5h16M1 9h16M1 13h16M5 5v4M12 5v4M8 9v4M14 9v4" stroke="#3a8fd5" stroke-width="1.6" fill="none"/></svg>Walls</span>
  <span><svg viewBox="0 0 18 18"><path d="M2 15h14M4 15V6M14 15V6M2 6h14M4 10h10" stroke="#2eb0c0" stroke-width="1.6" fill="none"/></svg>Terraces</span>
  <span><svg viewBox="0 0 18 18"><rect x="2" y="4" width="14" height="10" rx="2" stroke="#2aa64a" stroke-width="1.8" fill="none"/><path d="M5 9h8" stroke="#2aa64a" stroke-width="1.8"/></svg>Paths</span>
  <span><svg viewBox="0 0 18 18"><path d="M2 6h14l-3 7H5z" fill="#e09a22"/><path d="M9 13v4" stroke="#e09a22" stroke-width="2"/></svg>Outdoor kitchens</span>
  <span><svg viewBox="0 0 18 18"><rect x="2" y="3" width="14" height="13" stroke="#e04545" stroke-width="1.8" fill="none"/><path d="M9 14c-3-2-1-5 0-7 1 2 3 5 0 7z" fill="#e04545"/></svg>Fireplaces</span>
  <span><svg viewBox="0 0 18 18"><path d="M9 2c3 4 5 7 5 10a5 5 0 01-10 0c0-3 2-6 5-10z" fill="#e8b526"/></svg>Smokeries</span>
  <span><svg viewBox="0 0 18 18"><path d="M3 4v12M7 4v12M11 4v12M15 4v12M1 8h16M1 12h16" stroke="#9b59d6" stroke-width="1.6" fill="none"/></svg>Fences</span>
</div>
<div class="abs service-photo" style="left:723px;top:934px;width:377px;height:236px;background:linear-gradient(135deg,#e2d7c4,#bfb29c 55%,#8b7f6b)" role="img" aria-label="Photo of gloved hands chiselling a block of pale stone"></div>

<div class="abs divider" style="top:1198px"></div>

<!-- Restoration -->
<div class="abs service-photo" style="left:98px;top:1224px;width:377px;height:236px;background:linear-gradient(135deg,#9a9a9a,#6c5a48 55%,#3a2e24)" role="img" aria-label="Photo of workers restoring the timber frame and boards of a roof"></div>
<h3 class="abs service-name" style="left:509px;top:1220px">Restoration</h3>
<p class="abs service-copy" style="left:512px;top:1266px;width:535px">It's good to see that fixing old things has become popular again in recent years and people are trying to find ways to preserve valuable old windows and pieces of furniture before deciding to replace them. It is possible to give a new life to almost any wooden door, window, piece of furniture or staircase. The extensive experience of our craftsmen will help you achieve the desired result.</p>
<div class="abs tags" style="left:512px;top:1432px">
  <span><svg viewBox="0 0 18 18"><path d="M4 2h10v7H4zM3 9h12v3H3zM4 12v5M14 12v5" stroke="#2aa64a" stroke-width="2" fill="none"/></svg>Furniture</span>
  <span><svg viewBox="0 0 18 18"><rect x="2" y="3" width="14" height="12" fill="#f0b43a"/><path d="M9 3v12M2 9h14" stroke="#fff" stroke-width="1.5"/></svg>Windows</span>
  <span><svg viewBox="0 0 18 18"><path d="M4 1h10v17H4z" fill="#3a7bd5"/><circle cx="11.5" cy="10" r="1" fill="#fff"/></svg>Doors</span>
  <span><svg viewBox="0 0 18 18"><path d="M2 16h4v-4h4V8h4V4h3" stroke="#9b59d6" stroke-width="2" fill="none"/></svg>Staircases</span>
  <span><svg viewBox="0 0 18 18"><path d="M9 1l4 4-4 4-4-4zM9 9l4 4-4 4-4-4z" fill="#2eb0c0"/></svg>Floors</span>
  <span><svg viewBox="0 0 18 18"><path d="M2 15l8-10 6 4-6 6z" fill="#e8b526"/></svg>Special Projects</span>
</div>

<!-- About -->
<section class="abs about">
  <div class="abs service-photo" style="left:98px;top:37px;width:515px;height:351px;background:linear-gradient(160deg,#8a5a32,#c8935e 45%,#e6c79c 80%,#b07a45)" role="img" aria-label="Photo of an interior with wooden beams, a panelled door, a carved wooden screen and a pine floor"></div>
  <h2 class="abs about-title"><span class="cap">A</span>BOUT US</h2>
  <div class="abs about-copy">
    <p>Praxelun is a company whose business operations include making wooden products, restoration and building structures from natural stone. All of our products are made by craftsmen and specialists who have extensive experience and knowledge in their fields.</p>
    <p>The products we offer are always handmade and we take the requests and ideas of the specific client into account. We always strive to achieve the best possible quality.</p>
  </div>
  <div class="abs signoff">QUALITY MATTERS,<strong>PRAXELUN</strong></div>
</section>

<!-- Contact -->
<section class="abs contact" role="img" aria-label="Background photo of a chisel and wood shavings, darkened"></section>
<h2 class="abs section-title light" style="top:1977px"><span class="cap">C</span>ONTACT US</h2>

<h4 class="abs col-title" style="left:98px;top:2055px">CONTACT INFORMATION</h4>
<div class="abs info-row" style="top:2114px">
  <span class="info-icon"><svg width="16" height="18" viewBox="0 0 16 18"><path d="M8 17s6-6 6-10A6 6 0 002 7c0 4 6 10 6 10z" stroke="#fff" stroke-width="1.8" fill="none"/><circle cx="8" cy="7" r="2" fill="#fff"/></svg></span>
  <span>Kaskeda 12<br>10115 Tallinn<br>ESTONIA</span>
</div>
<div class="abs info-row" style="top:2172px">
  <span class="info-icon"><svg width="18" height="13" viewBox="0 0 18 13"><rect x="0" y="0" width="18" height="13" rx="2" fill="#fff"/><path d="M1 1l8 6 8-6" stroke="#4a3e33" stroke-width="1.5" fill="none"/></svg></span>
  <span>hello@praxelun.ee</span>
</div>
<div class="abs info-row" style="top:2228px">
  <span class="info-icon"><svg width="16" height="16" viewBox="0 0 16 16"><path d="M3 1l3 3-2 2c1 2 3 4 5 5l2-2 3 3-2 3C7 15 1 9 1 3z" fill="#fff"/></svg></span>
  <span>+372 55 18 302</span>
</div>
<h4 class="abs col-title" style="left:98px;top:2288px">SOCIAL</h4>
<div class="abs social-row"><i></i><i></i><i></i><i></i><i></i></div>

<h4 class="abs col-title" style="left:374px;top:2055px">PLEASE FILL IN THE FOLLOWING FIELDS IF YOU WOULD LIKE A PRICE QUOTE</h4>
<label class="abs field-label" style="left:374px;top:2093px">NAME :</label>
<span class="abs field" style="left:374px;top:2113px;width:357px;height:33px"></span>
<label class="abs field-label" style="left:741px;top:2093px">PHONE NO :</label>
<span class="abs field" style="left:741px;top:2113px;width:359px;height:33px"></span>
<label class="abs field-label" style="left:374px;top:2155px">EMAIL :</label>
<span class="abs field" style="left:374px;top:2175px;width:726px;height:33px"></span>
<label class="abs field-label" style="left:374px;top:2216px">MESSAGE :</label>
<span class="abs field" style="left:374px;top:2234px;width:726px;height:82px"></span>
<span class="abs btn-send">SEND</span>

<footer class="abs site-footer">Copyright © 2016, Praxelun. All Rights Reserved.</footer>

</body>
</html>
```